Tarn Workforce Tri Fold Brochure

My company is a recruiting/staffing firm. I need a design that is going to be professional, bright, young, hip and fun. Pictures are key! We want people working in an office, packaging, food production and/or light industrial environment. Must embrace DIVERSITY. Please use the 4 primary colors from the Tarn Logo to accent the piece, but not too busy. I am including the content that I would like to be included in the trifold as well as a sample of a trifold I have used in the past in addition to a couple of logos. My website is www.TarnWorkforce-example.com for look and feel.

Target Market(s)

Logistics, Distribution and Manufacturing companies

Industry/Entity Type

Staffing

Requirements
Must have
• Clean, colorful, eye catching, great pictures and graphics. Photo's of diverse people working, in a office, or production setting.
Nice to have
• Must be professional
Should not have
• Not too busy.

```html
<!DOCTYPE html>
<html lang="en">
<head>
<meta charset="utf-8">
<title>Tarn Workforce Tri Fold Brochure</title>
<link rel="stylesheet" href="https://fonts.googleapis.com/css2?family=Roboto+Condensed:wght@400;700&family=Roboto:wght@400;500;700&display=swap">
<style>
:root{
  --navy:#25235f;
  --red:#c8161d;
  --yellow:#f5cf10;
  --green:#2e9a3e;
  --ink:#111;
  --paper:#fff;
  --backdrop:#6d6d6d;
}
*{box-sizing:border-box;margin:0;padding:0}
html,body{width:900px;height:1200px;overflow:hidden;background:var(--backdrop)}
body{font-family:"Roboto",Arial,sans-serif;color:var(--ink);position:relative}
.brochure{position:absolute;left:30px;top:275px;width:840px;height:650px;background:var(--paper);box-shadow:0 6px 18px rgba(0,0,0,.35);overflow:hidden}
.panel{position:absolute;top:0;height:650px;text-align:center}
.panel--left{left:0;width:284px}
.panel--middle{left:284px;width:277px;background:linear-gradient(90deg,#e6e6e6 0,#fff 10%,#fff 90%,#e6e6e6 100%)}
.panel--right{left:561px;width:279px}
.photo{position:absolute;display:block}
.label{position:absolute;font-family:"Roboto Condensed",Arial,sans-serif;font-weight:700;color:#fff;display:flex;align-items:center;justify-content:center;text-transform:uppercase}
.label--red{background:var(--red)}
.label--navy{background:var(--navy)}
.copy{position:absolute;left:14px;right:14px;font-size:11px;line-height:1.35}
.band{position:absolute;left:0;right:0;display:flex;align-items:center;justify-content:center}
.band--yellow{background:var(--yellow)}
.phone{font-size:22px;color:var(--navy);font-weight:400}
.phone b{font-weight:700}
.web{position:absolute;left:0;right:0;font-size:11px;letter-spacing:2px;font-weight:700;color:var(--ink)}
.state{position:absolute;left:0;right:0;font-size:14px;line-height:1.55}
.state h3{color:var(--red);font-size:17px;font-weight:500;text-transform:uppercase}
.brand{position:absolute;top:40px;left:0;right:0;display:flex;align-items:center;justify-content:center;gap:8px;font-size:32px;font-weight:700;color:var(--navy)}
.brand__dot{width:12px;height:12px;border-radius:50%;background:var(--green)}
.navy-field{position:absolute;left:0;right:0;top:150px;height:330px;background:var(--navy)}
.headline{position:absolute;left:0;right:0;top:383px;color:#fff;font-family:"Roboto Condensed",Arial,sans-serif;line-height:1.1}
.headline__lead{font-size:16px}
.headline__mid{font-size:22px;font-weight:700}
.headline__big{font-size:32px;font-weight:700;color:var(--yellow)}
.red-band{position:absolute;left:0;right:0;top:487px;height:60px;background:var(--red);color:#fff;font-size:13px;line-height:1.35;display:flex;align-items:center;justify-content:center}
</style>
</head>
<body>
<main class="brochure">
  <section class="panel panel--left">
    <div class="photo" style="left:0;top:0;width:284px;height:215px;background:linear-gradient(160deg,#c9c4bd,#8f8176 55%,#c08d52)" role="img" aria-label="Worker in gloves tending a conveyor of baked goods in a food production line"></div>
    <div class="label label--red" style="left:12px;top:203px;width:268px;height:32px;font-size:15px">Definition of Tarn – Verb</div>
    <p class="copy" style="top:254px;font-size:12px;font-weight:700">To be in harmony or accord; To Fit; Agree</p>
    <p class="copy" style="top:276px;font-size:10px">“Yes the candidate meets the requirements, yeah they have the skills, but do they Tarn?”</p>
    <div class="label label--navy" style="left:94px;top:334px;width:96px;height:30px;font-size:16px">Mission</div>
    <p class="copy" style="top:378px;font-size:10px">At TARN Workforce, we are passionate in our pursuit to change lives by connecting great people with great organizations.</p>
    <div class="photo" style="left:0;top:430px;width:284px;height:130px;background:linear-gradient(180deg,#fff,#d8d4d0 40%,#3a3a48)" role="img" aria-label="Diverse group of smiling young professionals standing in a row"></div>
    <div class="band band--yellow" style="top:560px;height:47px"><span class="phone">+1 555-<b>210</b>-4400</span></div>
    <p class="web" style="top:623px">www.tarnworkforce-example.com</p>
  </section>

  <section class="panel panel--middle">
    <div class="photo" style="left:0;top:0;width:277px;height:200px;background:linear-gradient(180deg,rgba(120,125,135,.35),rgba(200,200,205,.35) 60%,rgba(255,255,255,0))" role="img" aria-label="Faded view of colleagues working together at a laptop"></div>
    <div class="label label--navy" style="left:53px;top:203px;width:170px;height:24px;font-size:15px">Contact Us</div>
    <div class="state" style="top:240px">
      <h3>Georgia</h3>
      <p>Cartersville – 555-201-1101</p>
      <p>Marietta – 555-201-1102</p>
      <p>Savannah – 555-201-1103</p>
      <p>Union City – 555-201-1104</p>
    </div>
    <div class="state" style="top:385px">
      <h3>Indiana</h3>
      <p>Plainfield – 555-201-1105</p>
    </div>
    <div class="state" style="top:460px">
      <h3>Pennsylvania</h3>
      <p>Harrisburg – 555-201-1106</p>
      <p>Bethlehem – 555-201-1107</p>
    </div>
    <div class="state" style="top:555px">
      <h3>Texas</h3>
      <p>Arlington – 555-201-1108</p>
    </div>
  </section>

  <section class="panel panel--right">
    <div class="brand"><span class="brand__dot"></span>Tarn Workforce</div>
    <div class="navy-field"></div>
    <div class="photo" style="left:22px;top:130px;width:236px;height:230px;border:4px solid #fff;background:linear-gradient(170deg,#e2ddd8,#9b8f86 45%,#2f2f3c);box-shadow:0 2px 6px rgba(0,0,0,.3)" role="img" aria-label="Confident team of diverse professionals in business attire"></div>
    <div class="headline">
      <p class="headline__lead">Take the first step</p>
      <p class="headline__mid">TOWARD A BETTER</p>
      <p class="headline__big">OPPORTUNITY</p>
    </div>
    <div class="red-band"><p>At Tarn Workforce, we are interested<br>in improving lives.</p></div>
    <div class="band" style="top:555px;height:48px"><span class="phone">+1 555-<b>210</b>-4400</span></div>
    <div class="band band--yellow" style="top:608px;height:42px"><span class="web" style="position:static">www.tarnworkforce-example.com</span></div>
  </section>
</main>
</body>
</html>
```